Brightway Haus Inc. Business Card Design

Brightway Haus Inc. is in search of a great clean design for our business cards!

Looking to incorporate our full logo and watermark on side one (however, I am open to having the text and watermark separated within the design.)

On side two, I am looking to have contact information (Name, Position, Phone #, Email, Website (www.thebrightwayhaus.ca). Can have the logo and/or watermark as part of the design if applicable.

Please add tagline "Where Shine Counts" on either side 1 or 2. This tagline can be in a sans serif, serif or cursive font as long as it compliments overall design. Capitalization can be title or sentence case depending on how it fits within the design.

Get creative!! Looking for a clean, crisp, premium design! Looking for a glossy card finish with spot UV features when printed. Cards will also be printed with rounded corners. Standard dimensions (3.5 x 2).

Target Market(s)

B2B - primary clients are business owners or property management corporations. (residential jobs are few and far between)

Industry/Entity Type

Business

Contact Information for Business Card

- clean, crisp design
- double sided
- spot UV accents and glossy finish upon printing
- standard business card size (3.5 x 2) with rounded corners
- please see project description for requirements per side

Font styles to use
Sans Serif

Requirements
Must have
• - adequate bleeds with print ready files
• - cohesive design elements between side 1 & 2
• - spot UV elements (can be on both sides or just one, use your discretion)
• - colour pallet should match the logo file provided
• - incorporate tagline "where shine counts" (this tagline can be in a serif or sans serif font as long as it is complimentary to the overall design.
Nice to have
• - Premium elements with a clean design
Should not have
• - Please omit cartoon or whimsical like designs, think premium.
• - Colours should not stray from the pallet of the provided logo.

```html
<!DOCTYPE html>
<html lang="en">
<head>
<meta charset="UTF-8">
<title>Brightway Haus Inc. Business Card</title>
<link rel="stylesheet" href="https://fonts.googleapis.com/css2?family=Open+Sans:wght@400;700;800&family=Roboto:wght@400;500&display=swap">
<style>
  :root {
    --backdrop: #565656;
    --card: #1d1e20;
    --card-edge: #141516;
    --gloss-dark: #262729;
    --gloss-light: #55575a;
    --accent: #1fb2bd;
    --text-soft: #c9c9c9;
    --text-muted: #8c8c8c;
  }
  * { margin: 0; padding: 0; box-sizing: border-box; }
  html, body {
    width: 799px;
    height: 1200px;
    overflow: hidden;
    background: var(--backdrop);
  }
  .canvas {
    position: relative;
    width: 799px;
    height: 1200px;
  }
  .card {
    position: absolute;
    left: 80px;
    width: 640px;
    height: 366px;
    background: var(--card);
    border-radius: 14px;
    overflow: hidden;
    box-shadow: 0 10px 30px rgba(0,0,0,0.45);
  }
  .card--front { top: 150px; }
  .card--back { top: 690px; }

  /* Front side */
  .front-mark {
    position: absolute;
    left: 50%;
    top: 50%;
    transform: translate(-50%, -50%);
    display: flex;
    flex-direction: column;
    align-items: center;
    gap: 18px;
  }
  .front-mark__square {
    width: 96px;
    height: 96px;
    background: linear-gradient(135deg, var(--gloss-light) 0%, var(--gloss-dark) 70%);
  }
  .front-mark__name {
    font-family: "Open Sans", sans-serif;
    font-weight: 800;
    font-size: 26px;
    letter-spacing: 1px;
    color: #3b3d40;
    text-transform: uppercase;
  }

  /* Back side */
  .gloss-panel {
    position: absolute;
    right: -40px;
    top: 120px;
    width: 300px;
    height: 300px;
    background: linear-gradient(140deg, var(--gloss-light) 0%, var(--gloss-dark) 55%, var(--card-edge) 100%);
  }
  .brand {
    position: absolute;
    left: 34px;
    top: 30px;
  }
  .brand__name {
    font-family: "Open Sans", sans-serif;
    font-weight: 800;
    font-size: 34px;
    line-height: 1;
    color: var(--accent);
    text-transform: uppercase;
    letter-spacing: -0.5px;
  }
  .brand__tagline {
    margin-top: 4px;
    font-family: "Open Sans", sans-serif;
    font-size: 13px;
    letter-spacing: 5.2px;
    color: var(--text-muted);
  }
  .contact {
    position: absolute;
    left: 34px;
    top: 118px;
    font-family: "Roboto", sans-serif;
    color: var(--text-soft);
  }
  .contact__name {
    font-family: "Open Sans", sans-serif;
    font-weight: 700;
    font-size: 22px;
    color: var(--accent);
  }
  .contact__role {
    font-size: 12px;
    color: var(--text-muted);
    margin-bottom: 18px;
  }
  .contact__address {
    font-size: 14px;
    line-height: 1.35;
    margin-bottom: 12px;
  }
  .contact__list { list-style: none; }
  .contact__item {
    display: flex;
    align-items: center;
    gap: 10px;
    font-size: 14px;
    line-height: 1.6;
  }
  .contact__icon { width: 13px; height: 13px; fill: var(--accent); flex: none; }
  .contact__web-accent { color: var(--accent); }
</style>
</head>
<body>
<main class="canvas">

  <section class="card card--front" aria-label="Card front">
    <div class="front-mark">
      <div class="front-mark__square"></div>
      <div class="front-mark__name">Brightway Haus Inc.</div>
    </div>
  </section>

  <section class="card card--back" aria-label="Card back">
    <div class="gloss-panel"></div>

    <header class="brand">
      <div class="brand__name">Brightway Haus Inc.</div>
      <div class="brand__tagline">Where Shine Counts</div>
    </header>

    <div class="contact">
      <div class="contact__name">Daniel Reyes</div>
      <div class="contact__role">Managing Director</div>
      <div class="contact__address">48 Harbour Lane,<br>Suite 2, Canada 204</div>
      <ul class="contact__list">
        <li class="contact__item">
          <svg class="contact__icon" viewBox="0 0 16 16" aria-hidden="true"><path d="M3 1h3l1.5 4-2 1.2a9 9 0 0 0 4.3 4.3L11 8.5l4 1.5v3a2 2 0 0 1-2 2A13 13 0 0 1 1 3a2 2 0 0 1 2-2z"/></svg>
          1800-555-0147
        </li>
        <li class="contact__item">
          <svg class="contact__icon" viewBox="0 0 16 16" aria-hidden="true"><path d="M1 3h14v10H1z M1 3l7 6 7-6" fill="none" stroke="#1fb2bd" stroke-width="1.6"/></svg>
          daniel@brightwayhaus.ca
        </li>
        <li class="contact__item">
          <svg class="contact__icon" viewBox="0 0 16 16" aria-hidden="true"><circle cx="8" cy="8" r="6.5" fill="none" stroke="#1fb2bd" stroke-width="1.5"/><path d="M1.5 8h13M8 1.5c-3 3.5-3 9.5 0 13M8 1.5c3 3.5 3 9.5 0 13" fill="none" stroke="#1fb2bd" stroke-width="1.2"/></svg>
          <span>www.<span class="contact__web-accent">thebrightwayhaus</span>.ca</span>
        </li>
      </ul>
    </div>
  </section>

</main>
</body>
</html>
```